Marwick Family Chiropractic Stationary

The letterhead and business card must have our logo.
We would like to see the logo used in different ways ( It can be expanded upon in the stationary.)
Please use the the same or similar colors.
Must be eye catching and memorable.
Must be easy to read

Reason: The doctor has been too busy to make any final decisions. He would like to give himself a little more time.

Target Market(s)

Chiropractic Healthcare

Industry/Entity Type

Business

Requirements
Must have
• Dr. Leonard Marwick D.C.
Chiropractor

860-555-0183

417 Birchfield Road, Suite 2
Kelton, CT 06091

drmarwick@marwickspine.example
www.marwickspine.example
www.facebook.com/MarwickFamilySpine
Should not have
• should not be difficult to read

```html
<!DOCTYPE html>
<html lang="en">
<head>
<meta charset="utf-8">
<title>Marwick Family Chiropractic – Business Card</title>
<link rel="stylesheet" href="https://fonts.googleapis.com/css2?family=Questrial&display=swap">
<style>
  :root {
    --stage: #3a3a3a;
    --card-white: #ffffff;
    --card-black: #1e1e1e;
    --green: #2e9e3e;
    --leaf-light: #9cc94a;
    --olive: #b7a722;
    --ink: #2a2a2a;
    --grey: #7a7a7a;
    --url-grey: #c9c9c9;
  }
  * { margin: 0; padding: 0; box-sizing: border-box; }
  html, body {
    width: 1200px; height: 900px; overflow: hidden;
    background: var(--stage);
    font-family: "Questrial", "Century Gothic", sans-serif;
  }
  .canvas { position: relative; width: 1200px; height: 900px; }
  .card {
    position: absolute; left: 285px; width: 630px; height: 360px;
    border-radius: 4px; box-shadow: 0 14px 30px rgba(0,0,0,.45);
    overflow: hidden;
  }
  .card-back { top: 70px; background: var(--card-black); }
  .card-front { top: 470px; background: var(--card-white); }

  /* back */
  .back-mark {
    position: absolute; left: 0; right: 0; top: 110px;
    display: flex; align-items: center; justify-content: center; gap: 16px;
  }
  .mark-dot { width: 46px; height: 46px; border-radius: 50%; background: var(--leaf-light); }
  .back-name { color: var(--leaf-light); font-size: 30px; letter-spacing: .5px; }
  .back-url {
    position: absolute; left: 0; right: 0; bottom: 70px; text-align: center;
    color: var(--url-grey); font-size: 17px; letter-spacing: .5px;
  }

  /* front */
  .doctor { position: absolute; left: 48px; top: 46px; }
  .doctor-name { color: var(--green); font-size: 27px; letter-spacing: .3px; }
  .doctor-title { color: var(--grey); font-size: 19px; margin-top: 2px; }
  .wordmark { position: absolute; left: 48px; top: 138px; color: var(--green); }
  .wordmark-main { font-size: 50px; line-height: 1; letter-spacing: 2px; }
  .wordmark-sub { font-size: 13px; letter-spacing: 1.2px; margin-top: 4px; }
  .contact { position: absolute; left: 48px; top: 222px; list-style: none; color: var(--grey); font-size: 16px; }
  .contact li { display: flex; gap: 10px; align-items: flex-start; line-height: 22px; margin-bottom: 4px; }
  .contact svg { flex: none; margin-top: 4px; }
  .mark-area {
    position: absolute; right: 45px; top: 70px; width: 200px; height: 200px;
    border-radius: 50%; background: radial-gradient(circle, #c6df7a, var(--leaf-light));
  }
</style>
</head>
<body>
<div class="canvas">
  <section class="card card-back">
    <div class="back-mark">
      <span class="mark-dot"></span>
      <span class="back-name">Marwick Family Chiropractic</span>
    </div>
    <p class="back-url">www.marwickspine.example</p>
  </section>

  <section class="card card-front">
    <div class="doctor">
      <p class="doctor-name">Dr. Leonard Marwick D.C.</p>
      <p class="doctor-title">Chiropractor</p>
    </div>
    <div class="wordmark">
      <p class="wordmark-main">MARWICK</p>
      <p class="wordmark-sub">FAMILY CHIROPRACTIC</p>
    </div>
    <ul class="contact">
      <li>
        <svg width="14" height="18" viewBox="0 0 14 18"><path d="M7 0a7 7 0 0 0-7 7c0 5 7 11 7 11s7-6 7-11a7 7 0 0 0-7-7zm0 10a3 3 0 1 1 0-6 3 3 0 0 1 0 6z" fill="var(--olive)"/></svg>
        <span>417 Birchfield Road,<br>Suite 2 Kelton, CT 06091</span>
      </li>
      <li>
        <svg width="16" height="14" viewBox="0 0 16 14"><path d="M1 4c0-2 3-3 7-3s7 1 7 3v1h-4V3.5H5V5H1zM3 6h10l1 7H2z" fill="var(--olive)"/></svg>
        <span>860-555-0183</span>
      </li>
      <li>
        <svg width="16" height="12" viewBox="0 0 16 12"><rect x="0.5" y="0.5" width="15" height="11" fill="none" stroke="var(--olive)" stroke-width="1.5"/><path d="M1 1l7 6 7-6" fill="none" stroke="var(--olive)" stroke-width="1.5"/></svg>
        <span>drmarwick@marwickspine.example</span>
      </li>
    </ul>
    <div class="mark-area" role="img" aria-label="Practice emblem area"></div>
  </section>
</div>
</body>
</html>
```